holloway paving service

Needs to have phone number 0418259730 and email markholloway@brightmail.com.au.
ABN 62318470915
name mark holloway

For all your concreting solutions
Excavation
Exposed & colour concrete
House & shed slabs
Driveways
Landing & steps

Contact Information for Business Card

ph 0418259730
email markholloway@brightmail.com.au.
ABN 62318470915
name mark holloway

```html
<!DOCTYPE html>
<html lang="en">
<head>
<meta charset="utf-8">
<title>Holloway Paving Service – Business Card</title>
<link href="https://fonts.googleapis.com/css2?family=Montserrat:wght@500;600&family=Lato:wght@400&display=swap" rel="stylesheet">
<style>
  :root {
    --backdrop: #1c1c1d;
    --card: #161617;
    --orange: #ec6a22;
    --white: #f2f2f2;
    --muted: #bdbdbd;
    --rule: #d9d9d9;
  }
  * { box-sizing: border-box; margin: 0; padding: 0; }
  html, body { width: 1200px; height: 900px; overflow: hidden; }
  body {
    background: var(--backdrop);
    position: relative;
    font-family: "Lato", sans-serif;
    color: var(--white);
  }
  .card {
    position: absolute;
    left: 250px;
    width: 700px;
    height: 400px;
    background: var(--card);
    box-shadow: 0 10px 30px rgba(0,0,0,.45);
  }
  .card--front { top: 30px; }
  .card--back { top: 470px; }

  /* brand lockup */
  .brand { display: flex; align-items: center; gap: 18px; }
  .brand__mark { width: 26px; height: 26px; background: var(--orange); flex: none; }
  .brand__divider { width: 2px; height: 78px; background: var(--orange); flex: none; }
  .brand__text { display: flex; flex-direction: column; align-items: center; }
  .brand__name {
    font-family: "Montserrat", sans-serif;
    font-weight: 600;
    font-size: 22px;
    color: var(--orange);
    letter-spacing: .5px;
    text-transform: uppercase;
    white-space: nowrap;
  }
  .brand__phone {
    display: flex; align-items: center; gap: 10px;
    margin-top: 4px;
    font-family: "Montserrat", sans-serif;
    font-weight: 500;
    font-size: 15px;
    color: var(--orange);
    letter-spacing: 4px;
  }
  .brand__phone::before, .brand__phone::after {
    content: ""; width: 44px; height: 2px; background: var(--rule);
  }

  .card--front .brand {
    position: absolute; left: 50%; top: 50%;
    transform: translate(-50%, -50%);
  }

  .card--back .brand { position: absolute; left: 44px; top: 40px; }
  .card--back .brand__name { font-size: 21px; }

  .person { position: absolute; left: 44px; top: 150px; }
  .person__name {
    font-family: "Montserrat", sans-serif;
    font-weight: 500;
    font-size: 30px;
    color: var(--orange);
    letter-spacing: 1.5px;
    text-transform: uppercase;
    white-space: nowrap;
  }
  .person__role { font-size: 17px; margin-top: 2px; }

  .address { position: absolute; left: 44px; top: 232px; font-size: 17px; line-height: 1.35; }
  .address__area { color: var(--orange); }

  .contact { position: absolute; left: 44px; top: 292px; list-style: none; font-size: 17px; line-height: 1.45; }
  .contact li { display: flex; align-items: center; gap: 10px; }
  .contact svg { width: 13px; height: 13px; flex: none; }
  .contact .accent { color: var(--orange); }

  /* services column */
  .services {
    position: absolute; left: 440px; top: 150px; width: 220px;
    padding-left: 20px; border-left: 2px solid var(--orange);
  }
  .services__tagline {
    font-family: "Montserrat", sans-serif;
    font-weight: 500;
    font-size: 14px;
    color: var(--orange);
    line-height: 1.35;
    margin-bottom: 10px;
  }
  .services__list { list-style: none; font-size: 16px; line-height: 1.55; }
  .services__list li { display: flex; align-items: center; gap: 9px; }
  .services__list li::before {
    content: ""; width: 6px; height: 6px; background: var(--orange); flex: none;
  }
  .services__abn { margin-top: 12px; font-size: 15px; color: var(--muted); letter-spacing: .5px; }
  .services__abn span { color: var(--orange); }
</style>
</head>
<body>

<section class="card card--front">
  <div class="brand">
    <span class="brand__mark"></span>
    <span class="brand__divider"></span>
    <div class="brand__text">
      <span class="brand__name">Holloway Paving Service</span>
      <span class="brand__phone">0418259730</span>
    </div>
  </div>
</section>

<section class="card card--back">
  <div class="brand">
    <div class="brand__text">
      <span class="brand__name">Holloway Paving Service</span>
      <span class="brand__phone">0418259730</span>
    </div>
  </div>

  <div class="person">
    <p class="person__name">Mark Holloway</p>
    <p class="person__role">Director</p>
  </div>

  <div class="address">
    <p class="address__area">Sorell Creek</p>
    <p>Tasmania 7140</p>
  </div>

  <ul class="contact">
    <li>
      <svg viewBox="0 0 24 24" aria-hidden="true"><path fill="#ec6a22" d="M6.6 10.8a15 15 0 0 0 6.6 6.6l2.2-2.2a1 1 0 0 1 1-.25 11.4 11.4 0 0 0 3.6.57 1 1 0 0 1 1 1V20a1 1 0 0 1-1 1A17 17 0 0 1 3 4a1 1 0 0 1 1-1h3.5a1 1 0 0 1 1 1c0 1.25.2 2.45.57 3.57a1 1 0 0 1-.25 1z"/></svg>
      +61 418 259 730
    </li>
    <li>
      <svg viewBox="0 0 24 24" aria-hidden="true"><rect x="2" y="5" width="20" height="14" fill="none" stroke="#ec6a22" stroke-width="2.4"/><path d="M2 6l10 7 10-7" fill="none" stroke="#ec6a22" stroke-width="2.4"/></svg>
      markholloway@brightmail.com.au
    </li>
    <li>
      <svg viewBox="0 0 24 24" aria-hidden="true"><circle cx="12" cy="12" r="10" fill="none" stroke="#ec6a22" stroke-width="2.2"/><path d="M2 12h20M12 2c3 3 3 17 0 20M12 2c-3 3-3 17 0 20" fill="none" stroke="#ec6a22" stroke-width="2"/></svg>
      <span>www.<span class="accent">hollowaypaving</span>.com.au</span>
    </li>
  </ul>

  <div class="services">
    <p class="services__tagline">For all your concreting solutions</p>
    <ul class="services__list">
      <li>Excavation</li>
      <li>Exposed &amp; colour concrete</li>
      <li>House &amp; shed slabs</li>
      <li>Driveways</li>
      <li>Landing &amp; steps</li>
    </ul>
    <p class="services__abn"><span>ABN</span> 62318470915</p>
  </div>
</section>

</body>
</html>
```